PWNF Traditional Business Card Project

Please see attached....just a simple business card... on attachment- please use the exact font, style, etc as the attached "Ned Farley Broughton" card... however, replace with the "Walter Augustin Pryde" text and address below the card.

```html
<!DOCTYPE html>
<html lang="en">
<head>
<meta charset="utf-8">
<title>PWNF Business Card</title>
<link rel="stylesheet" href="https://fonts.googleapis.com/css2?family=Playfair+Display+SC:wght@700&family=Questrial&display=swap">
<style>
  :root {
    --page-bg: #ececed;
    --card-frame: #8c8d8e;
    --card-face: #c8cacb;
    --corner-mark: #e4e5e6;
    --ink: #111111;
    --ink-soft: #1c1c1c;
  }
  * { margin: 0; padding: 0; box-sizing: border-box; }
  html, body {
    width: 1200px;
    height: 857px;
    overflow: hidden;
    background: var(--page-bg);
  }
  .canvas {
    position: relative;
    width: 1200px;
    height: 857px;
    display: flex;
    align-items: center;
    justify-content: center;
  }
  .business-card {
    position: relative;
    width: 980px;
    height: 560px;
    background: var(--card-frame);
    padding: 18px;
    box-shadow: 0 6px 18px rgba(0,0,0,0.18);
  }
  .card-face {
    position: relative;
    width: 100%;
    height: 100%;
    background: var(--card-face);
    color: var(--ink);
  }
  .corner-mark {
    position: absolute;
    width: 34px;
    height: 34px;
  }
  .corner-mark.top-left { top: 0; left: 0; }
  .corner-mark.top-right { top: 0; right: 0; transform: scaleX(-1); }
  .corner-mark.bottom-left { bottom: 0; left: 0; transform: scaleY(-1); }
  .corner-mark.bottom-right { bottom: 0; right: 0; transform: scale(-1,-1); }

  .firm {
    position: absolute;
    top: 34px;
    left: 40px;
  }
  .firm-name {
    font-family: "Playfair Display SC", serif;
    font-weight: 700;
    font-size: 40px;
    letter-spacing: 2px;
    line-height: 1;
  }
  .firm-sub {
    font-family: "Questrial", sans-serif;
    font-size: 15px;
    letter-spacing: 3px;
    text-transform: uppercase;
    margin-top: 8px;
    margin-left: 4px;
  }

  .attorney {
    position: absolute;
    top: 170px;
    left: 104px;
  }
  .attorney-name {
    font-family: "Playfair Display SC", serif;
    font-weight: 700;
    font-size: 52px;
    letter-spacing: 2px;
    line-height: 1;
    white-space: nowrap;
  }
  .attorney-title {
    font-family: "Questrial", sans-serif;
    font-size: 19px;
    letter-spacing: 9px;
    text-transform: uppercase;
    margin-top: 10px;
    text-align: center;
    padding-left: 60px;
  }

  .contact {
    position: absolute;
    font-family: "Questrial", sans-serif;
    font-size: 20px;
    line-height: 1.3;
    letter-spacing: 1px;
    color: var(--ink-soft);
  }
  .contact.address {
    left: 40px;
    bottom: 36px;
    text-transform: uppercase;
  }
  .contact.address .web { text-transform: none; }
  .contact.reach {
    right: 56px;
    bottom: 36px;
  }
  .contact.reach .line-upper { text-transform: uppercase; }
</style>
</head>
<body>
<main class="canvas">
  <article class="business-card">
    <div class="card-face">
      <svg class="corner-mark top-left" viewBox="0 0 34 34" aria-hidden="true"><path d="M0 0H34V8H8V34H0Z" fill="var(--corner-mark)"/></svg>
      <svg class="corner-mark top-right" viewBox="0 0 34 34" aria-hidden="true"><path d="M0 0H34V8H8V34H0Z" fill="var(--corner-mark)"/></svg>
      <svg class="corner-mark bottom-left" viewBox="0 0 34 34" aria-hidden="true"><path d="M0 0H34V8H8V34H0Z" fill="var(--corner-mark)"/></svg>
      <svg class="corner-mark bottom-right" viewBox="0 0 34 34" aria-hidden="true"><path d="M0 0H34V8H8V34H0Z" fill="var(--corner-mark)"/></svg>

      <header class="firm">
        <div class="firm-name">Pacific Western</div>
        <div class="firm-sub">Norland Firm, PLC</div>
      </header>

      <section class="attorney">
        <h1 class="attorney-name">Walter Augustin Pryde</h1>
        <p class="attorney-title">Attorney at Law</p>
      </section>

      <address class="contact address" style="font-style:normal">
        2470 Cedar Lane, Suite B<br>
        Arbor Falls, CA 90000<br>
        <span class="web">www.lawspwnf.com</span>
      </address>

      <address class="contact reach" style="font-style:normal">
        <span class="line-upper">Tel (555) 214-3800</span><br>
        <span class="line-upper">Fax (555) 214-3801</span><br>
        wpryde@lawspwnf.com
      </address>
    </div>
  </article>
</main>
</body>
</html>
```